UK landscaping company needs website

We, Brackwell Landscapes need a website design for a company based in Surrey, UK. The design should be bold and playful. We have three main areas of work driveways, paving and fencing. It shouldn't be too heavy in text and concentrate on the pictures from previous jobs we've completed. You may use stock images for the design, these can be changed if you are successful. Please don’t just copy the flyer it is just there to provide content.
We have a logo design which we would also like editing slightly.
Here are some of my local competitors
https://www.pelmarlandscapes.example.co.uk/

https://www.twinfirgardendesign.example.com/

https://kestbyrnlandscapes.example.co.uk/

Industry/Entity Type

Landscaping

Coding

Coded - Design and coding required

Number of Pages Required

3 page

Font styles to use
Sans Serif

Requirements
Must have
• Pictures of my previous jobs.
Must be mobile friendly
Easy to navigate
Nice to have
• Try to use different colours. It would be good to have some designs that aren’t just black and green.
I’d like some curves in the design.
Should not have
• We install hard landscaping. Think more building/construction and less plants and cutting grass.

```html
<!DOCTYPE html>
<html lang="en">
<head>
<meta charset="utf-8">
<title>Brackwell Landscapes</title>
<link href="https://fonts.googleapis.com/css2?family=Archivo:wght@600;700;800&family=Poppins:wght@400;500;600&display=swap" rel="stylesheet">
<style>
:root{
  --green:#5cb531;
  --green-dark:#3f8f1f;
  --blue:#1565c0;
  --blue-field:#2f86e6;
  --dark:#2b2b2b;
  --darker:#232323;
  --ink:#1e1e1e;
  --text:#4a4a4a;
  --white:#ffffff;
  --grey-band:#f2f2f2;
}
*{box-sizing:border-box;margin:0;padding:0}
html,body{width:1200px;height:4332px;overflow:hidden}
body{position:relative;font-family:"Poppins",sans-serif;color:var(--text);background:var(--white)}
.abs{position:absolute}
.heading{font-family:"Archivo",sans-serif;font-weight:800;color:var(--ink);letter-spacing:-0.5px}
.heading .accent{color:var(--green)}
.photo{position:absolute}

/* header */
.site-header{position:absolute;left:0;top:0;width:1200px;height:70px;background:var(--dark);z-index:5}
.brand{position:absolute;left:131px;top:20px;font-family:"Archivo",sans-serif;font-weight:800;font-size:24px;color:var(--white);letter-spacing:0.5px}
.nav a{position:absolute;top:26px;font-family:"Archivo",sans-serif;font-weight:700;font-size:15px;color:var(--white);text-decoration:none}
.header-cta{position:absolute;right:0;top:0;width:200px;height:70px;background:var(--green);color:var(--white);padding:14px 0 0 27px}
.header-cta small{display:block;font-family:"Archivo",sans-serif;font-weight:700;font-size:13px}
.header-cta strong{display:block;font-family:"Archivo",sans-serif;font-weight:700;font-size:21px;line-height:1.1}

/* hero */
.hero-title{left:131px;top:214px;font-size:51px;line-height:56px;color:var(--white);width:680px}
.hero-points{left:131px;top:402px;list-style:none}
.hero-points li{display:flex;align-items:center;gap:12px;color:var(--white);font-family:"Archivo",sans-serif;font-weight:600;font-size:20px;height:37px}
.btn{display:inline-flex;align-items:center;gap:10px;color:var(--white);font-family:"Archivo",sans-serif;font-weight:700;font-size:17px;text-decoration:none;justify-content:center}
.btn-green{background:var(--green);left:131px;top:540px;width:188px;height:49px}
.btn-blue{background:var(--blue-field)}

/* estimate form */
.estimate{left:607px;top:573px;width:458px;height:536px;background:var(--blue);box-shadow:0 6px 18px rgba(0,0,0,.25);color:var(--white);text-align:center;padding-top:34px}
.estimate h2{font-family:"Archivo",sans-serif;font-weight:800;font-size:25px}
.estimate p{font-size:14px;line-height:21px;margin-top:6px}
.field{position:absolute;background:var(--blue-field);border:1px solid #6aa9ef;color:var(--white);font-family:"Archivo",sans-serif;font-weight:600;font-size:13px;text-align:left;padding:0 15px;display:flex;align-items:center}
.field.area{align-items:flex-start;padding-top:16px}
.select-caret{position:absolute;left:1000px;top:817px;width:40px;height:37px;background:var(--blue);display:flex;align-items:center;justify-content:center}

/* about */
.about-title{left:130px;top:898px;font-size:45px}
.about-text{left:130px;top:963px;width:435px;font-size:16.5px;line-height:24px;color:#444}

/* services */
.section-title{width:1200px;text-align:center;font-size:45px}
.service-label{position:absolute;font-family:"Archivo",sans-serif;font-weight:700;font-size:28px;color:var(--white);text-align:center;width:260px}

/* why */
.why-title{top:1770px;color:var(--white)}
.why-rule{left:562px;top:1830px;width:76px;height:3px;background:var(--green)}
.why-intro{left:230px;top:1848px;width:740px;text-align:center;color:#e5e5e5;font-size:17px;line-height:30px}
.feature{position:absolute;width:220px;text-align:center;color:var(--white)}
.feature .icon{width:94px;height:94px;border:2px solid #f0f0f0;border-radius:50%;margin:0 auto;display:flex;align-items:center;justify-content:center}
.feature h3{font-weight:500;font-size:22px;margin-top:24px}
.feature p{font-size:13px;line-height:19px;margin-top:10px;color:#e5e5e5}

/* work grid */
.work-tile{position:absolute}
.view-more{background:rgba(21,101,192,.85);display:flex;flex-direction:column;align-items:center;justify-content:center;color:var(--white);font-family:"Archivo",sans-serif;font-weight:600;font-size:28px;gap:26px}
.view-more .ring{width:44px;height:44px;border-radius:50%;background:var(--white);display:flex;align-items:center;justify-content:center}

/* testimonial */
.testimonial-band{left:0;top:3313px;width:1200px;height:257px;background:var(--grey-band)}
.arrow-btn{position:absolute;width:40px;height:40px;border-radius:50%;display:flex;align-items:center;justify-content:center}
.quote{left:433px;top:3383px;width:450px;font-size:14px;line-height:21px;color:#333}
.review-meta{left:433px;top:3460px;font-family:"Archivo",sans-serif;font-weight:700;font-size:13px;color:#222;display:flex;gap:18px;align-items:center}
.stars{color:#f5a623;letter-spacing:3px;font-size:14px}

/* cta */
.cta-title{left:0;top:3634px;width:1200px;text-align:center;color:var(--white);font-size:30px;line-height:41px;font-family:"Archivo",sans-serif;font-weight:800;letter-spacing:-0.8px}
.btn-cta{left:480px;top:3738px;width:241px;height:46px;background:var(--blue-field)}

/* footer */
.footer{left:0;top:3950px;width:1200px;height:382px;background:var(--darker)}
.footer-brand{left:133px;top:4070px;font-family:"Archivo",sans-serif;font-weight:800;font-size:28px;color:var(--white);line-height:32px}
.footer-col{position:absolute;top:4047px;list-style:none}
.footer-col li{font-family:"Archivo",sans-serif;font-weight:700;font-size:14px;color:var(--white);line-height:36px}
.footer-col li.link{font-family:"Poppins",sans-serif;font-weight:400;font-size:13px;text-decoration:underline;line-height:27px}
.social{position:absolute;top:4206px;width:32px;height:32px;border:1.5px solid #bdbdbd;border-radius:50%}
.footer-rule{left:0;top:4262px;width:1200px;height:1px;background:#444}
.copyright{left:0;top:4282px;width:1200px;text-align:center;color:#cfcfcf;font-size:14px}
</style>
</head>
<body>

<!-- hero photo -->
<div class="photo" role="img" aria-label="Aerial view of a landscaped estate with pool, patio and woodland" style="left:0;top:70px;width:1200px;height:860px;background:linear-gradient(160deg,#2f4a3a 0%,#3b6a34 35%,#4d7f35 60%,#2c4f22 100%)"></div>
<svg class="abs" style="left:0;top:680px" width="1200" height="340" viewBox="0 0 1200 340">
  <path d="M0 230 C300 70 800 40 1200 60 L1200 340 L0 340 Z" fill="#ffffff"/>
  <path d="M1065 50 C1120 55 1165 70 1200 82" stroke="#5cb531" stroke-width="8" fill="none"/>
  <path d="M0 226 C60 190 110 165 160 145" stroke="#5cb531" stroke-width="8" fill="none"/>
</svg>

<header class="site-header">
  <div class="brand">BRACKWELL LANDSCAPES</div>
  <nav class="nav">
    <a style="left:475px">HOME</a>
    <a style="left:563px">SERVICES</a>
    <a style="left:680px">ABOUT</a>
    <a style="left:774px">OUR WORK</a>
    <a style="left:899px">CONTACT</a>
  </nav>
  <div class="header-cta"><small>FREE ESTIMATES</small><strong>(000) 888 - 888</strong></div>
</header>

<h1 class="abs heading hero-title">Your lawn and landscape cared for the way they should be</h1>
<ul class="abs hero-points">
  <li><svg width="22" height="22" viewBox="0 0 22 22"><circle cx="11" cy="11" r="9" fill="none" stroke="#fff" stroke-width="2"/><path d="M6.5 11.5l3 3 6-6" fill="none" stroke="#fff" stroke-width="2"/></svg>40 Years Combined Experience</li>
  <li><svg width="22" height="22" viewBox="0 0 22 22"><circle cx="11" cy="11" r="9" fill="none" stroke="#fff" stroke-width="2"/><path d="M6.5 11.5l3 3 6-6" fill="none" stroke="#fff" stroke-width="2"/></svg>EXTRAORDINARY LAWN &amp; GARDEN CARE</li>
  <li><svg width="22" height="22" viewBox="0 0 22 22"><circle cx="11" cy="11" r="9" fill="none" stroke="#fff" stroke-width="2"/><path d="M6.5 11.5l3 3 6-6" fill="none" stroke="#fff" stroke-width="2"/></svg>QUALITY THAT IS GUARANTEED</li>
</ul>
<a class="abs btn btn-green">GET STARTED <svg width="17" height="17" viewBox="0 0 17 17"><circle cx="8.5" cy="8.5" r="8" fill="#fff"/><path d="M7 5l3.5 3.5L7 12" stroke="#5cb531" stroke-width="2" fill="none"/></svg></a>

<form class="abs estimate">
  <h2>GET A FREE ESTIMATE</h2>
  <p>Fill out out form below and a representative<br>will be in touch.</p>
</form>
<div class="field" style="left:633px;top:710px;width:194px;height:35px">NAME</div>
<div class="field" style="left:845px;top:710px;width:196px;height:35px">PHONE</div>
<div class="field" style="left:633px;top:764px;width:194px;height:35px">EMAIL</div>
<div class="field" style="left:845px;top:764px;width:196px;height:35px">ADDRESS</div>
<div class="field" style="left:633px;top:818px;width:408px;height:35px">ESTIMATE TYPE</div>
<div class="select-caret"><svg width="14" height="8" viewBox="0 0 14 8"><path d="M0 0h14L7 8z" fill="#fff"/></svg></div>
<div class="field area" style="left:633px;top:872px;width:408px;height:107px">HOW CAN WE HELP ?</div>
<a class="abs btn btn-blue" style="left:800px;top:998px;width:241px;height:46px;font-size:16px;font-weight:600">START MY ESTIMATE <svg width="17" height="17" viewBox="0 0 17 17"><circle cx="8.5" cy="8.5" r="8" fill="#fff"/><path d="M7 5l3.5 3.5L7 12" stroke="#2f86e6" stroke-width="2" fill="none"/></svg></a>

<h2 class="abs heading about-title">ABOUT <span class="accent">BRACKWELL</span></h2>
<p class="abs about-text">Lorem Ipsum is simply dummy text of the printing and typesetting industry. Lorem Ipsum has industry's standard dummy text ever since the 1500s, when an unknown printer took a galley of type and scrambled Lorem Ipsum is simply dummy text of the printing and typesetting industry.</p>

<h2 class="abs heading section-title" style="left:0;top:1234px">OUR <span class="accent">SERVICES</span></h2>

<!-- why choose us band -->
<div class="photo" role="img" aria-label="Garden with timber fence, lawn and decking at dusk" style="left:0;top:1440px;width:1200px;height:833px;background:linear-gradient(135deg,#2e2723 0%,#3a322b 45%,#354a2a 80%,#3f6127 100%)"></div>
<svg class="abs" style="left:0;top:1400px" width="1200" height="300" viewBox="0 0 1200 300">
  <path d="M0 0 H1200 V90 C900 70 400 120 0 300 Z" fill="#ffffff"/>
  <path d="M1040 82 C1100 78 1150 78 1200 82" stroke="#5cb531" stroke-width="16" fill="none"/>
  <path d="M0 275 C50 250 100 232 150 215 L150 240 C100 255 50 275 0 300 Z" fill="#5cb531"/>
</svg>

<!-- service circles -->
<svg class="abs" style="left:135px;top:1340px" width="940" height="360" viewBox="0 0 940 360">
  <circle cx="168" cy="175" r="160" fill="#5cb531"/>
  <circle cx="168" cy="175" r="136" fill="#fff"/>
  <circle cx="769" cy="175" r="160" fill="#5cb531"/>
  <circle cx="769" cy="175" r="136" fill="#fff"/>
  <circle cx="465" cy="180" r="178" fill="#1565c0"/>
  <circle cx="465" cy="180" r="152" fill="#fff"/>
</svg>
<div class="photo" role="img" aria-label="Block-paved driveway in front of a house" style="left:172px;top:1384px;width:262px;height:262px;border-radius:50%;background:linear-gradient(180deg,#8a8f96 0%,#5b5f6f 50%,#3c3f55 100%)"></div>
<div class="photo" role="img" aria-label="Swimming pool surrounded by stone paving" style="left:453px;top:1373px;width:295px;height:295px;border-radius:50%;background:linear-gradient(180deg,#4b5a66 0%,#3aa3d6 40%,#a58f77 75%,#7c6a57 100%)"></div>
<div class="photo" role="img" aria-label="Timber decking and lawn beside a house" style="left:773px;top:1384px;width:262px;height:262px;border-radius:50%;background:linear-gradient(180deg,#c9b48a 0%,#a98e5f 45%,#4f8a2a 75%,#3b6f21 100%)"></div>
<div class="service-label" style="left:173px;top:1560px">DRIVEWAYS</div>
<div class="service-label" style="left:470px;top:1566px">PAVING</div>
<div class="service-label" style="left:775px;top:1560px">FENCING</div>

<h2 class="abs heading section-title why-title" style="left:0">WHY CHOOSE US?</h2>
<div class="abs why-rule"></div>
<p class="abs why-intro">Lorem Ipsum is simply dummy text of the printing and typesetting industry. Lorem Ipsum hasindustry's standard dummy text</p>

<div class="feature" style="left:202px;top:1939px">
  <div class="icon"><svg width="50" height="50" viewBox="0 0 50 50"><circle cx="25" cy="25" r="23" fill="#1565c0"/><circle cx="29" cy="20" r="8" fill="none" stroke="#fff" stroke-width="3"/><path d="M23 26L13 36" stroke="#fff" stroke-width="4"/></svg></div>
  <h3>Professionalism</h3>
  <p>Use our body field scanner, at home to uncover why yhou feelthe way you do</p>
</div>
<div class="feature" style="left:497px;top:1939px">
  <div class="icon"><svg width="50" height="50" viewBox="0 0 50 50"><circle cx="25" cy="25" r="23" fill="#1565c0"/><path d="M14 25l8 8 15-16" stroke="#fff" stroke-width="4" fill="none"/></svg></div>
  <h3>Better Results</h3>
  <p>Use our body field scanner, at home to uncover why yhou feelthe way you do</p>
</div>
<div class="feature" style="left:777px;top:1939px">
  <div class="icon"><svg width="50" height="50" viewBox="0 0 50 50"><path d="M12 14h26M12 25h26M12 36h26" stroke="#1565c0" stroke-width="3" stroke-dasharray="5 4"/><circle cx="12" cy="14" r="4" fill="#1565c0"/><circle cx="38" cy="25" r="4" fill="#1565c0"/><circle cx="12" cy="36" r="4" fill="#1565c0"/></svg></div>
  <h3>Quality Work</h3>
  <p>Use our body field scanner, at home to uncover why yhou feelthe way you do</p>
</div>

<h2 class="abs heading section-title" style="left:0;top:2338px">LATEST <span class="accent">WORK</span></h2>

<div class="work-tile" role="img" aria-label="Lawn and paved steps beside a brick wall" style="left:136px;top:2438px;width:457px;height:269px;background:linear-gradient(160deg,#7a5a45,#4f8a2a 55%,#9a9a96)"></div>
<div class="work-tile" role="img" aria-label="Curved block-paved driveway in front of a white house" style="left:602px;top:2438px;width:458px;height:269px;background:linear-gradient(180deg,#b8bcc0,#9b8577 55%,#7d6a60)"></div>
<div class="work-tile" role="img" aria-label="Timber sleeper steps, lawn and fence" style="left:136px;top:2717px;width:303px;height:268px;background:linear-gradient(170deg,#6b5340,#4f8a2a 55%,#b0a090)"></div>
<div class="work-tile" role="img" aria-label="Pergola over a paved patio" style="left:447px;top:2717px;width:301px;height:268px;background:linear-gradient(180deg,#6f8fb0,#4d6f93)"></div>
<div class="work-tile view-more" style="left:447px;top:2717px;width:301px;height:268px"><span class="ring"><svg width="18" height="18" viewBox="0 0 18 18"><path d="M7 3H3v12h12v-4M10 3h5v5M15 3L8 10" stroke="#1565c0" stroke-width="1.8" fill="none"/></svg></span>View More</div>
<div class="work-tile" role="img" aria-label="New timber fence along a lawn" style="left:758px;top:2717px;width:302px;height:268px;background:linear-gradient(180deg,#7aa0c0,#9a7a52 45%,#4f8a2a 80%)"></div>
<div class="work-tile" role="img" aria-label="Swimming pool with sandstone paving" style="left:136px;top:2995px;width:457px;height:269px;background:linear-gradient(180deg,#6a5648,#3aa3d6 35%,#b2957a 65%,#8c755f)"></div>
<div class="work-tile" role="img" aria-label="Grey block paving beside artificial lawn" style="left:602px;top:2995px;width:458px;height:269px;background:linear-gradient(160deg,#a58f70,#4f8a2a 40%,#808386 70%,#5f6266)"></div>

<div class="abs testimonial-band"></div>
<div class="arrow-btn" style="left:198px;top:3404px;border:2px solid #5cb531"><svg width="14" height="14" viewBox="0 0 14 14"><path d="M9 2L4 7l5 5" stroke="#5cb531" stroke-width="2" fill="none"/></svg></div>
<div class="arrow-btn" style="left:961px;top:3404px;background:#5cb531"><svg width="14" height="14" viewBox="0 0 14 14"><path d="M5 2l5 5-5 5" stroke="#fff" stroke-width="2" fill="none"/></svg></div>
<div class="photo" role="img" aria-label="Portrait of happy customers" style="left:311px;top:3385px;width:94px;height:93px;background:linear-gradient(180deg,#d8cfc4,#b89a80)"></div>
<svg class="abs" style="left:397px;top:3468px" width="22" height="22" viewBox="0 0 22 22"><rect width="22" height="22" fill="#5cb531"/><circle cx="11" cy="11" r="6" fill="none" stroke="#fff" stroke-width="1.5"/><path d="M8 11l2 2 4-4" stroke="#fff" stroke-width="1.5" fill="none"/></svg>
<p class="abs quote">"They did an excellent job. It great! It only took on day, and the installers did and excellent job cleaning up...I highly recommend them if you went a professional job done right"</p>
<div class="abs review-meta"><span>CUSTOMER NAME</span><span>|</span><span>TRUSTVALE REVIEW</span><span>|</span><span class="stars">★★★★★</span></div>

<!-- cta band -->
<div class="photo" role="img" aria-label="Landscaped front garden with flowering shrubs and lawn" style="left:0;top:3570px;width:1200px;height:420px;background:linear-gradient(180deg,#5a6a4a 0%,#6b7d55 30%,#3f6d2a 70%,#2f5a20 100%)"></div>
<h2 class="abs cta-title">WE TAKE CARE OF YOUR LANDSCAPE.<br>YOU TAKE BACK YOUR FREE TIME.</h2>
<a class="abs btn btn-cta" style="font-weight:600;font-size:16px">START MY ESTIMATE <svg width="17" height="17" viewBox="0 0 17 17"><circle cx="8.5" cy="8.5" r="8" fill="#fff"/><path d="M7 5l3.5 3.5L7 12" stroke="#2f86e6" stroke-width="2" fill="none"/></svg></a>

<div class="abs footer"></div>
<svg class="abs" style="left:0;top:3900px" width="1200" height="120" viewBox="0 0 1200 120">
  <path d="M0 120 C300 40 800 20 1200 10 L1200 120 Z" fill="#232323"/>
  <path d="M150 70 C400 25 800 12 1200 8 L1200 20 C800 24 450 40 150 70 Z" fill="#5cb531"/>
</svg>
<div class="abs footer-brand">BRACKWELL<br><span style="font-size:14px">LANDSCAPES</span></div>
<ul class="footer-col" style="left:385px"><li>HOME</li><li>ABOUT US</li><li>OUR WORK</li><li>CONTACT</li></ul>
<ul class="footer-col" style="left:504px"><li>SERVICES</li><li class="link">Driveways</li><li class="link">Paving</li><li class="link">Fencing</li></ul>
<ul class="footer-col" style="left:633px"><li>QUICK LINKS</li><li class="link">FAQ</li><li class="link">Testimonials</li><li class="link">Sitemap</li></ul>
<div class="photo" role="img" aria-label="Street map showing the company location" style="left:786px;top:4049px;width:281px;height:109px;background:linear-gradient(135deg,#e6ebef,#d4dde3);border-bottom:4px solid #f5a623"></div>
<svg class="abs" style="left:916px;top:4086px" width="16" height="22" viewBox="0 0 16 22"><path d="M8 0a8 8 0 0 0-8 8c0 6 8 14 8 14s8-8 8-14a8 8 0 0 0-8-8z" fill="#d62b3a"/><circle cx="8" cy="8" r="3" fill="#fff"/></svg>
<div class="social" style="left:525px"></div>
<div class="social" style="left:564px"></div>
<div class="social" style="left:603px"></div>
<div class="social" style="left:643px"></div>
<div class="abs footer-rule"></div>
<p class="abs copyright">© 2020 Brackwell Landscapes. All Rights are Reserved.</p>

</body>
</html>
```